Cyber Security Site Design (Products & Consulting)

I need my website redesigned to be engaging, clean, efficient and modern. My company (when its up and running) is going to be concentrated on two things: a few specific products for cyber security as well as cyber security consulting services. The background I bring to the field is having worked with small companies all the way to the largest government organizations and advising them on their security posture and how to improve it. We need the ability to add products and services easily.

For a sample product, you can use either Tarnet (http://www.tarnet-relay.org/) or Verodyne Ashmantle (https://www.verodyne.com/products/relay-hx-and-fortified-edge-portal).

It will replace https://lumerafieldworks.com/

Target Market(s)

Cyber Security professionals in all verticals

Coding

Coded - Design and coding required

Number of Pages Required

4 page

Font styles to use
Sans Serif

Colors
6b449b

Requirements
Must have
• Ability to easily modify
• Have main page
• Have product specific pages
• Have consulting services pages
• Have executive team information
• Clean, modern design
• Usage of the logo and its color scheme
Nice to have
• I like the idea of a left collapsed sidebar (so icons only) that can expand for text.
• I am also open to a very unique landing page, possibly a shape in the middle (hexagons maybe?) with each of the options there.
Should not have
• Nothing that looks like it came out of a hacker movie

```html
<!DOCTYPE html>
<html lang="en">
<head>
<meta charset="utf-8">
<title>Lumera Fieldworks — Cyber Security Consulting</title>
<link rel="stylesheet" href="https://fonts.googleapis.com/css2?family=Montserrat:wght@400;500;600;700&family=Open+Sans:wght@400;600&display=swap">
<style>
:root{
  --purple:#6b449b;
  --purple-dark:#4f2f78;
  --purple-light:#8a63bb;
  --ink:#1d1d24;
  --text:#555a63;
  --muted:#8b8f97;
  --line:#d9d9de;
  --grey-band:#e6e6ea;
  --row:#ececef;
  --white:#ffffff;
  --night:#1b1530;
  --foot:#2c2c33;
}
*{box-sizing:border-box;margin:0;padding:0}
html,body{width:1200px;height:4100px;overflow:hidden}
body{font-family:"Open Sans",Arial,sans-serif;color:var(--text);background:var(--white);position:relative}
.abs{position:absolute}
h1,h2,h3,h4,.nav a,.btn{font-family:"Montserrat",Arial,sans-serif}
svg{display:block}

/* header */
.topbar{top:0;right:0;width:520px;height:36px;background:#3a3a42;display:flex;align-items:center;justify-content:flex-end;gap:34px;padding-right:142px;color:#fff;font-size:13px;border-bottom-left-radius:4px}
.topbar span{display:flex;align-items:center;gap:8px}
.brand{top:46px;left:142px;display:flex;align-items:center;gap:12px}
.brand .mark{width:54px;height:54px;background:var(--purple);border-radius:50%}
.brand .name{font-family:"Montserrat",Arial,sans-serif;font-weight:600;color:var(--purple);font-size:30px;letter-spacing:1px;line-height:1}
.nav{top:76px;left:546px;display:flex;gap:44px}
.nav a{font-size:14px;font-weight:600;color:var(--ink);text-decoration:none;letter-spacing:.5px}
.nav a.active{border-bottom:2px solid var(--purple);padding-bottom:4px}

/* hero */
.hero{top:130px;left:0;width:1200px;height:567px;background:radial-gradient(circle at 75% 35%,#9ab7f0 0%,#4a6ac0 22%,#243a84 50%,#141e4a 100%)}
.hero-copy{top:330px;left:142px;color:#fff}
.hero-copy h1{font-size:35px;font-weight:700;line-height:45px;letter-spacing:.5px}
.btn-hero{top:494px;left:142px;height:44px;padding:0 22px 0 12px;background:var(--purple);color:#fff;font-size:15px;font-weight:500;display:flex;align-items:center;gap:12px;border-radius:0 22px 22px 0}
.btn-hero i{width:28px;height:28px;border-radius:50%;background:#fff;display:block}

/* section heads */
.sec-title{left:0;width:1200px;text-align:center;color:var(--ink);font-size:28px;font-weight:700;letter-spacing:.5px}
.sec-title small{font-size:13px;color:var(--purple);font-weight:600}
.divider{left:536px;width:128px;height:20px;display:flex;align-items:center;gap:12px}
.divider b{flex:1;height:1px;background:#777}
.divider i{width:16px;height:16px;border-radius:50%;background:var(--purple)}
.divider.light b{background:rgba(255,255,255,.6)}
.lead{left:140px;width:920px;text-align:center;font-size:15px;line-height:25px}

/* about */
.about-line{top:1088px;left:355px;width:492px;height:1px;background:var(--line)}
.circle{width:116px;height:116px;border-radius:50%;background:#fff;box-shadow:0 3px 14px rgba(0,0,0,.12);display:flex;align-items:center;justify-content:center}
.item{width:240px;text-align:center}
.item h4{font-size:15px;font-weight:500;color:var(--ink);margin:22px 0 8px;text-transform:uppercase}
.item p{font-size:13px;line-height:20px}
.chev{color:var(--ink);font-size:18px;margin-top:8px;font-weight:700;letter-spacing:-3px}

/* services */
.band-grey{top:1317px;left:0;width:1200px;height:336px;background:linear-gradient(120deg,#ececf0 0%,#dcdce2 50%,#e9e9ee 100%)}
.svc .item h4{font-weight:700;font-size:14px}

/* team */
.photo{top:1957px;left:142px;width:298px;height:398px;background:linear-gradient(180deg,#d9d9de 0%,#b7b7bf 55%,#4a4a55 100%)}
.socials{top:2355px;left:142px;width:298px;height:50px;background:#e6e6ea;display:flex;align-items:center;justify-content:center;gap:10px}
.socials i{width:24px;height:24px;border-radius:50%;background:var(--purple);display:block}
.bio{top:1950px;left:486px;width:574px}
.bio h3{font-size:25px;font-weight:600;color:var(--ink)}
.bio .role{font-family:"Montserrat",Arial,sans-serif;font-size:14px;font-weight:600;color:var(--ink);margin-top:8px}
.bio p{font-size:15px;line-height:25px;margin-top:30px}
.facts{top:2163px;left:486px;width:574px;font-size:13.5px;color:var(--ink)}
.facts div{display:flex;justify-content:space-between;height:38px;align-items:center;padding:0 24px}
.facts div:nth-child(odd){background:var(--row)}
.btn-team{top:2362px;left:645px;width:256px;height:46px;background:#e6e6ea;color:var(--ink);font-size:13.5px;font-weight:600;display:flex;align-items:center;justify-content:center}

/* products */
.products{top:2500px;left:0;width:1200px;height:717px;background:radial-gradient(ellipse at 50% 20%,#5a4488 0%,#2d2150 45%,var(--night) 100%)}
.card{top:2755px;width:434px;height:345px;background:#fff;border-radius:6px;box-shadow:0 4px 16px rgba(0,0,0,.25);text-align:center}
.card .shot{margin:20px auto 0;width:200px;height:170px;border-radius:6px}
.card h4{font-size:17px;font-weight:700;color:var(--ink);margin-top:32px}
.card p{font-size:14px;line-height:22px;margin:10px 60px 0}

/* contact */
.contact{top:3217px;left:0;width:1200px;height:418px;background:var(--purple)}
.contact-title{top:3300px;left:0;width:1200px;text-align:center;color:#fff;font-size:29px;font-weight:700;line-height:42px;letter-spacing:.5px}
.field{background:var(--purple-light);color:#e8def5;font-size:13px;padding:0 14px;display:flex;align-items:center;height:40px}
.field.area{align-items:flex-start;padding-top:12px}
.c-phone{top:3410px;left:740px;color:#fff;font-family:"Montserrat",Arial,sans-serif;font-size:26px;font-weight:500}
.c-note{top:3456px;left:742px;width:220px;color:#efe8f8;font-size:13px;line-height:20px}
.btn-submit{top:3510px;left:784px;width:142px;height:38px;background:#fff;color:var(--purple);font-size:15px;font-weight:600;display:flex;align-items:center;justify-content:center}

/* footer */
.f-brand{top:3685px;left:0;width:1200px;display:flex;justify-content:center;align-items:center;gap:14px}
.f-brand .mark{width:70px;height:70px;background:var(--purple);border-radius:50%}
.f-brand .name{font-family:"Montserrat",Arial,sans-serif;font-weight:600;color:var(--purple);font-size:38px;letter-spacing:1px}
.f-nav{top:3812px;left:0;width:1200px;display:flex;justify-content:center;align-items:center;gap:34px}
.f-nav a{font-family:"Montserrat",Arial,sans-serif;color:var(--ink);font-size:15px;text-decoration:none;letter-spacing:.5px}
.f-nav i{width:12px;height:12px;border-radius:50%;border:1.5px solid #bbb;display:block}
.f-col{top:3885px;width:300px;text-align:center}
.f-col .ic{margin:0 auto;width:50px;height:50px;display:flex;align-items:center;justify-content:center;position:relative}
.f-col .ic::before,.f-col .ic::after{content:"";position:absolute;top:25px;width:70px;height:1px;background:var(--line)}
.f-col .ic::before{right:60px}.f-col .ic::after{left:60px}
.f-col h4{font-size:15px;font-weight:500;color:var(--ink);margin-top:24px}
.f-col p{font-size:14px;color:var(--ink);margin-top:6px}
.copy{top:4053px;left:0;width:1200px;height:47px;background:var(--foot);color:#ddd;font-size:12px;display:flex;align-items:center;justify-content:center;letter-spacing:.5px}
</style>
</head>
<body>

<header>
  <div class="abs topbar">
    <span><svg width="14" height="14" viewBox="0 0 24 24"><path fill="#fff" d="M6.6 10.8a15 15 0 0 0 6.6 6.6l2.2-2.2c.3-.3.7-.4 1-.2 1.1.4 2.3.6 3.6.6.6 0 1 .4 1 1V20c0 .6-.4 1-1 1A17 17 0 0 1 3 4c0-.6.4-1 1-1h3.5c.6 0 1 .4 1 1 0 1.3.2 2.5.6 3.6.1.3 0 .7-.2 1z"/></svg>+123 456 8989</span>
    <span><svg width="15" height="12" viewBox="0 0 24 18"><rect x="1" y="1" width="22" height="16" rx="2" fill="none" stroke="#fff" stroke-width="2"/><path d="M1 2l11 8 11-8" fill="none" stroke="#fff" stroke-width="2"/></svg>inquiry@lumerafieldworks.com</span>
  </div>
  <div class="abs brand"><i class="mark"></i><span class="name">LUMERA<br><span style="font-size:13px;letter-spacing:5px">FIELDWORKS</span></span></div>
  <nav class="abs nav">
    <a class="active" href="#">HOME</a><a href="#">SERVICES</a><a href="#">OUR TEAM</a><a href="#">PRODUCTS</a><a href="#">CONTACT</a>
  </nav>
</header>

<section>
  <div class="abs hero" role="img" aria-label="Photo of a hand reaching toward a glowing padlock over a blue digital network backdrop"></div>
  <div class="abs hero-copy"><h1>WE PROVIDE EARLY DETECTION,<br>IMMEDIATE REMEDIATION AND<br>PROACTIVE PREVENTIVE MEASURES</h1></div>
  <a class="abs btn btn-hero"><i></i>CONTACT US TODAY</a>
</section>

<section>
  <h2 class="abs sec-title" style="top:783px">ABOUT LUMERA <small>FIELDWORKS</small></h2>
  <div class="abs divider" style="top:838px"><b></b><i></i><b></b></div>
  <p class="abs lead" style="top:882px">We are a company that takes its roots from the idea of providing appropriate and creative solutions for cyber security operations, development and management. We have a mission first mindset for our clients and their objectives.</p>
  <p class="abs lead" style="top:942px">We are located in the Ashford / Millbrook area but are able to work with clients world-wide. Please contact us for any inquires you may have and we will be glad to assist you in any way possible.</p>
  <div class="abs about-line"></div>
  <div class="abs item" style="top:1030px;left:235px">
    <div class="circle" style="margin:0 auto;width:100px;height:100px"><svg width="40" height="40" viewBox="0 0 40 40"><path d="M6 34L18 16l6 8 4-5 7 15z" fill="#2b2b33"/><path d="M18 16V4" stroke="#2b2b33" stroke-width="2"/><path d="M18 4h10l-2 3 2 3H18z" fill="var(--purple)"/></svg></div>
    <h4>Mission</h4><p>Lorem ipsum dolor sit<br>amet, consectetuer adipis</p><div class="chev">››</div>
  </div>
  <div class="abs circle" style="top:1020px;left:537px;width:126px;height:126px"><span style="font-family:Montserrat,Arial,sans-serif;font-weight:600;color:var(--purple);font-size:15px">LUMERA</span></div>
  <div class="abs item" style="top:1030px;left:727px">
    <div class="circle" style="margin:0 auto;width:100px;height:100px"><svg width="44" height="30" viewBox="0 0 44 30"><path d="M2 15C10 3 34 3 42 15 34 27 10 27 2 15z" fill="none" stroke="#2b2b33" stroke-width="2.5"/><circle cx="22" cy="15" r="8" fill="var(--purple)"/><circle cx="22" cy="15" r="3" fill="#fff"/></svg></div>
    <h4>Vision</h4><p>Lorem ipsum dolor sit<br>amet, consectetuer adipis</p><div class="chev">››</div>
  </div>
</section>

<section class="svc">
  <div class="abs band-grey"></div>
  <h2 class="abs sec-title" style="top:1402px;font-size:27px">CYBER SECURITY CONSULTING SERVICES</h2>
  <div class="abs divider" style="top:1462px"><b></b><i></i><b></b></div>
  <p class="abs lead" style="top:1504px;font-size:13.5px;line-height:22px;left:230px;width:740px">Lorem ipsum dolor sit amet, consectetuer adipiscing elit, sed diam nonummy nibh euismod tincidunt ut laoreet dolore magna aliquam erat volutpat. Ut wisi enim ad minim veniam</p>
  <div class="abs item" style="top:1593px;left:134px">
    <div class="circle" style="margin:0 auto"><svg width="46" height="40" viewBox="0 0 46 40"><rect x="3" y="3" width="40" height="27" rx="2" fill="none" stroke="#2b2b33" stroke-width="2"/><path d="M17 38h12M23 30v8" stroke="#2b2b33" stroke-width="2"/><path d="M23 9l7 3v5c0 4-3 7-7 8-4-1-7-4-7-8v-5z" fill="none" stroke="var(--purple)" stroke-width="2"/></svg></div>
    <h4>Virtual CISO / VISO</h4><p>Lorem ipsum dolor sit amet,<br>consectetuer adipiscing</p><div class="chev">››</div>
  </div>
  <div class="abs item" style="top:1593px;left:364px">
    <div class="circle" style="margin:0 auto"><svg width="40" height="44" viewBox="0 0 40 44"><path d="M20 3l15 6v11c0 10-7 18-15 21C12 38 5 30 5 20V9z" fill="none" stroke="#2b2b33" stroke-width="2"/><rect x="13" y="20" width="14" height="11" rx="1" fill="var(--purple)"/><path d="M15 20v-4a5 5 0 0 1 10 0v4" fill="none" stroke="var(--purple)" stroke-width="2"/></svg></div>
    <h4>Cyber Security</h4><p>Lorem ipsum dolor sit amet,<br>consectetuer adipiscing</p><div class="chev">››</div>
  </div>
  <div class="abs item" style="top:1593px;left:602px">
    <div class="circle" style="margin:0 auto"><svg width="46" height="42" viewBox="0 0 46 42"><circle cx="23" cy="9" r="5" fill="none" stroke="#2b2b33" stroke-width="2"/><circle cx="9" cy="30" r="5" fill="none" stroke="#2b2b33" stroke-width="2"/><circle cx="37" cy="30" r="5" fill="none" stroke="#2b2b33" stroke-width="2"/><path d="M20 14l-8 11M26 14l8 11M14 30h18" stroke="var(--purple)" stroke-width="2"/></svg></div>
    <h4>Risk Assessment</h4><p>Lorem ipsum dolor sit amet,<br>consectetuer adipiscing</p><div class="chev">››</div>
  </div>
  <div class="abs item" style="top:1593px;left:831px">
    <div class="circle" style="margin:0 auto"><svg width="46" height="42" viewBox="0 0 46 42"><circle cx="23" cy="21" r="6" fill="var(--purple)"/><path d="M23 3v12M23 27v12M5 21h12M29 21h12M10 8l8 8M36 8l-8 8M10 34l8-8M36 34l-8-8" stroke="#2b2b33" stroke-width="2"/></svg></div>
    <h4>Network Security</h4><p>Lorem ipsum dolor sit amet,<br>consectetuer adipiscing</p><div class="chev">››</div>
  </div>
</section>

<section>
  <div class="abs photo" role="img" aria-label="Portrait photo of the founder and CEO in a dark suit"></div>
  <div class="abs socials"><i></i><i></i><i></i><i></i></div>
  <div class="abs bio">
    <h3>Marcus Delaven Ostrander</h3>
    <div class="role">Founder &amp; CEO</div>
    <p>Marcus has been in the cyber security fields for over 10 years having worked as a contractor for various Federal agencies. His experiences have provided him the ability to look at the security posture of an organization and provide concise recommendations to improve it's stature.</p>
  </div>
  <div class="abs facts">
    <div><span>AGE :</span><span>48</span></div>
    <div><span>LOCATION :</span><span>Ashford / Millbrook, NC, USA</span></div>
    <div><span>EXPERIENCE :</span><span>10 Years</span></div>
    <div><span>PHONE :</span><span>123 456 7890</span></div>
  </div>
  <a class="abs btn btn-team">VIEW ALL TEAM MEMBERS</a>
</section>

<section>
  <div class="abs products" role="img" aria-label="Dark purple backdrop with a glowing circular tech pattern"></div>
  <h2 class="abs sec-title" style="top:2588px;color:#fff;font-size:27px;font-weight:600">CYBER SECURITY CONSULTING PRODUCTS</h2>
  <div class="abs divider light" style="top:2644px"><b></b><i></i><b></b></div>
  <p class="abs lead" style="top:2678px;font-size:13.5px;line-height:22px;left:230px;width:740px;color:#ddd">Lorem ipsum dolor sit amet, consectetuer adipiscing elit, sed diam nonummy nibh euismod tincidunt ut laoreet dolore magna aliquam erat volutpat. Ut wisi enim ad minim veniam</p>
  <div class="abs card" style="left:142px">
    <div class="shot" role="img" aria-label="Yellow software product box with disc" style="background:linear-gradient(160deg,#fff6b0,#f1d21c 60%,#c9a80a)"></div>
    <h4>PRODUCT 1</h4><p>Lorem ipsum dolor sit amet, consectetuer adipis cing elit, sed diam nonummy nibh euismod</p><div class="chev">››</div>
  </div>
  <div class="abs card" style="left:626px">
    <div class="shot" role="img" aria-label="Blue software product box with disc" style="background:linear-gradient(160deg,#e3f3ff,#5fb2ea 60%,#2b79b8)"></div>
    <h4>PRODUCT 2</h4><p>Lorem ipsum dolor sit amet, consectetuer adipis cing elit, sed diam nonummy nibh euismod</p><div class="chev">››</div>
  </div>
</section>

<section>
  <div class="abs contact"></div>
  <h2 class="abs contact-title">WE PROVIDE SECURITY SERVICES THAT MATCHES YOUR<br>NEEDS &amp; YOUR BUDGET!</h2>
  <div class="abs field" style="top:3405px;left:162px;width:263px">Name</div>
  <div class="abs field" style="top:3405px;left:435px;width:265px">Interested in</div>
  <div class="abs field" style="top:3455px;left:162px;width:263px">Phone</div>
  <div class="abs field area" style="top:3455px;left:435px;width:265px;height:90px">Enter Your Word</div>
  <div class="abs field" style="top:3505px;left:162px;width:263px">Email</div>
  <div class="abs c-phone">+ 123 456 7890</div>
  <p class="abs c-note">Lorem ipsum dolor sit amet, consectet adipiscing, sed diam tetuer adi</p>
  <a class="abs btn btn-submit">SUBMIT</a>
</section>

<footer>
  <div class="abs f-brand"><i class="mark"></i><span class="name">LUMERA</span></div>
  <nav class="abs f-nav"><a href="#">HOME</a><i></i><a href="#">SERVICES</a><i></i><a href="#">OUR TEAM</a><i></i><a href="#">PRODUCTS</a><i></i><a href="#">CONTACT</a></nav>
  <div class="abs f-col" style="left:162px">
    <div class="ic"><svg width="30" height="38" viewBox="0 0 30 38"><path d="M15 2C8 2 3 7 3 14c0 9 12 22 12 22s12-13 12-22C27 7 22 2 15 2z" fill="none" stroke="var(--purple)" stroke-width="3"/><circle cx="15" cy="14" r="4" fill="#2b2b33"/></svg></div>
    <h4>ADDRESS</h4><p>Ashford / Millbrook, NC, USA</p>
  </div>
  <div class="abs f-col" style="left:450px">
    <div class="ic"><svg width="34" height="34" viewBox="0 0 24 24"><path fill="none" stroke="var(--purple)" stroke-width="1.8" d="M6.6 10.8a15 15 0 0 0 6.6 6.6l2.2-2.2c.3-.3.7-.4 1-.2 1.1.4 2.3.6 3.6.6.6 0 1 .4 1 1V20c0 .6-.4 1-1 1A17 17 0 0 1 3 4c0-.6.4-1 1-1h3.5c.6 0 1 .4 1 1 0 1.3.2 2.5.6 3.6.1.3 0 .7-.2 1z"/></svg></div>
    <h4>PHONE</h4><p>+ 123 456 7890</p>
  </div>
  <div class="abs f-col" style="left:738px">
    <div class="ic"><svg width="36" height="28" viewBox="0 0 24 18"><rect x="1" y="1" width="22" height="16" rx="2" fill="none" stroke="var(--purple)" stroke-width="2"/><path d="M1 2l11 8 11-8" fill="none" stroke="#2b2b33" stroke-width="2"/></svg></div>
    <h4>EMAIL</h4><p>info@lumerafieldworks.com</p>
  </div>
  <div class="abs copy">COPYRIGHT © 2018 LUMERA FIELDWORKS. ALL RIGHTS RESERVED.</div>
</footer>

</body>
</html>
```